Got the awesome logo, now need the awesome business card

Want to use my just purchased logo on the backside of my card and to secure another logo by the same designer (Marcus) for the front side.

Reason: I have uploaded the logos. QVL7 should be on the front of the card with my contact information and Qvl7pex should be on the back. Thank you.

The logos have been uploaded and I have extended the deadline by 5 days. The QVL& logo should be on the front with my contact information and the qvl7pex should be on the back.

• Existing logo(s), clean background on front of card

```html
<!DOCTYPE html>
<html lang="en">
<head>
<meta charset="utf-8">
<title>Qvl7pex Business Card</title>
<link rel="stylesheet" href="https://fonts.googleapis.com/css2?family=Open+Sans:wght@400;700&display=swap">
<style>
  :root {
    --backdrop: #5f5c57;
    --card: #ffffff;
    --card-shade: #f1f1f1;
    --brand-blue: #2a7ac0;
    --brand-orange: #f28a1e;
    --ink: #3a3a3a;
    --ink-soft: #555555;
  }
  html, body {
    margin: 0;
    width: 1200px;
    height: 871px;
    overflow: hidden;
    background: var(--backdrop);
  }
  .canvas {
    position: relative;
    width: 1200px;
    height: 871px;
  }
  .card {
    position: absolute;
    width: 560px;
    height: 320px;
    background: linear-gradient(160deg, var(--card) 0%, var(--card-shade) 100%);
    box-shadow: 0 14px 30px rgba(0,0,0,0.35);
    overflow: hidden;
  }
  .card--back { left: 80px; top: 110px; }
  .card--front { left: 560px; top: 441px; background: var(--card); }

  .back-name {
    position: absolute;
    inset: 0;
    display: flex;
    align-items: center;
    justify-content: center;
    text-align: center;
    font-family: "Open Sans", sans-serif;
    font-weight: 700;
    font-size: 40px;
    line-height: 1.25;
    color: var(--brand-blue);
    margin: 0;
  }

  .front-name {
    position: absolute;
    left: 36px;
    top: 84px;
    width: 250px;
    margin: 0;
    font-family: "Open Sans", sans-serif;
    font-weight: 700;
    font-size: 30px;
    line-height: 1.25;
    color: var(--brand-blue);
  }

  .contact {
    position: absolute;
    left: 318px;
    top: 58px;
    font-family: "Open Sans", sans-serif;
    color: var(--ink);
  }
  .contact__name { font-weight: 700; font-size: 13px; margin: 0; }
  .contact__role { font-size: 11px; color: var(--ink-soft); margin: 2px 0 30px; }
  .contact__list { list-style: none; margin: 0; padding: 0; }
  .contact__item {
    display: flex;
    align-items: center;
    gap: 10px;
    font-size: 12px;
    height: 20px;
    color: var(--ink-soft);
  }
  .contact__icon { width: 12px; height: 12px; flex: none; }
  .contact__square { width: 11px; height: 11px; background: var(--brand-blue); flex: none; }

  .front-wave {
    position: absolute;
    left: 0; bottom: 0;
    width: 560px; height: 110px;
  }
</style>
</head>
<body>
<main class="canvas">
  <section class="card card--back" aria-label="Card back">
    <p class="back-name">Qvl7pex<br>Executive Management</p>
  </section>

  <section class="card card--front" aria-label="Card front">
    <p class="front-name">QVL7<br>Management</p>

    <div class="contact">
      <p class="contact__name">Dana Hollis</p>
      <p class="contact__role">Principal</p>
      <ul class="contact__list">
        <li class="contact__item">
          <svg class="contact__icon" viewBox="0 0 12 12" aria-hidden="true">
            <path d="M1 4 Q6 0 11 4 L9 5 L8 3.5 Q6 3 4 3.5 L3 5 Z" fill="var(--brand-orange)"/>
            <rect x="2.5" y="6" width="7" height="5" rx="1" fill="var(--brand-orange)"/>
          </svg>
          555.014.2290
        </li>
        <li class="contact__item">
          <svg class="contact__icon" viewBox="0 0 12 12" aria-hidden="true">
            <rect x="0.75" y="2.5" width="10.5" height="7.5" fill="none" stroke="var(--brand-orange)" stroke-width="1.3"/>
            <path d="M1 3 L6 7 L11 3" fill="none" stroke="var(--brand-orange)" stroke-width="1.3"/>
          </svg>
          qvl7management@mailpost.com
        </li>
        <li class="contact__item"><span class="contact__square"></span>@qvl7management</li>
        <li class="contact__item"><span class="contact__square"></span>DanaHollisExecMgmt</li>
      </ul>
    </div>

    <svg class="front-wave" viewBox="0 0 560 110" preserveAspectRatio="none" aria-hidden="true">
      <path d="M0 20 Q300 40 560 110 L0 110 Z" fill="var(--brand-orange)"/>
      <path d="M0 27 Q300 48 560 118 L560 110 L0 110 Z" fill="var(--brand-blue)"/>
    </svg>
  </section>
</main>
</body>
</html>
```